Consulting company requires a logo and business card design

I require a logo/business card design for a new company based in Sexsmith Alberta called TallMarsh Integrity Consulting Ltd. I plan to provide the following services: Construction management/inspection for the oil and gas industry, as well as general consulting for Asset Management, fleet management, etc. Have attached a copy of resume for use as guide for

Target Market(s)

Businesses within the oil and gas production, construction and shipping industry

Industry/Entity Type

Oil And Gas

Contact Information for Business Card

Believe should highlight, services offered, safety, quality,

Logo Text

TallMarsh Integrity Consulting (TMIC) ?

Font styles to use
Script

Requirements
Must have
• Open to all options

```html
<!DOCTYPE html>
<html lang="en">
<head>
<meta charset="utf-8">
<title>TallMarsh Integrity Consulting Ltd. – Business Card</title>
<link rel="stylesheet" href="https://fonts.googleapis.com/css2?family=Open+Sans:wght@400;600&display=swap">
<style>
  :root {
    --backdrop: #4a423d;
    --card: #0d0d0e;
    --card-edge: #1c1c1e;
    --brand-blue: #4fb6ee;
    --text-light: #e9ecef;
    --tagline-blue: #4a8fd6;
    --divider: #2a8fd0;
  }
  * { margin: 0; padding: 0; box-sizing: border-box; }
  html, body {
    width: 1200px; height: 900px; overflow: hidden;
    background: var(--backdrop);
    font-family: "Open Sans", Arial, sans-serif;
  }
  .canvas {
    position: relative; width: 1200px; height: 900px;
    background: radial-gradient(ellipse at 50% 40%, #5a514b 0%, var(--backdrop) 75%);
  }
  .card {
    position: absolute; top: 296px;
    width: 540px; height: 308px;
    background: var(--card);
    border: 1px solid var(--card-edge);
    box-shadow: 0 18px 40px rgba(0,0,0,.55);
  }
  .card--front { left: 40px; }
  .card--back  { left: 620px; }

  /* Brand name block (replaces mark) */
  .brand { display: flex; align-items: center; gap: 12px; }
  .brand__dot {
    width: 22px; height: 22px; border-radius: 50%;
    background: var(--brand-blue); flex: none;
  }
  .brand__name {
    color: var(--brand-blue); font-weight: 400;
    font-size: 22px; line-height: 1.25;
  }

  .card--front .brand { position: absolute; left: 38px; top: 120px; width: 230px; }
  .divider {
    position: absolute; left: 290px; top: 62px;
    width: 1px; height: 184px;
    background: linear-gradient(to bottom, transparent, var(--divider) 30%, var(--divider) 70%, transparent);
  }
  .contact { position: absolute; left: 314px; top: 66px; color: var(--text-light); }
  .contact__name { color: var(--brand-blue); font-weight: 600; font-size: 17px; }
  .contact__role { font-size: 14px; margin-bottom: 16px; }
  .contact__address { font-size: 14px; line-height: 1.35; margin-bottom: 14px; }
  .contact__list { list-style: none; font-size: 14px; line-height: 1.45; }
  .contact__list li { display: flex; align-items: center; gap: 9px; }
  .contact__list svg { width: 11px; height: 11px; fill: var(--brand-blue); flex: none; }

  .card--back .brand {
    position: absolute; left: 0; right: 0; top: 78px;
    justify-content: center;
  }
  .card--back .brand__name { font-size: 26px; text-align: left; }
  .tagline {
    position: absolute; left: 46px; right: 46px; top: 196px;
    color: var(--tagline-blue); font-size: 14px; line-height: 1.4;
    text-align: center;
  }
</style>
</head>
<body>
<main class="canvas">

  <section class="card card--front" aria-label="Business card front">
    <div class="brand">
      <span class="brand__dot"></span>
      <span class="brand__name">TallMarsh Integrity Consulting Ltd.</span>
    </div>
    <div class="divider"></div>
    <div class="contact">
      <p class="contact__name">Daniel Harper</p>
      <p class="contact__role">Managing Director</p>
      <p class="contact__address">4821, Ridgeview Road<br>Sexsmith, AB, T0H 3C0.</p>
      <ul class="contact__list">
        <li>
          <svg viewBox="0 0 12 12" aria-hidden="true"><path d="M2.4 0.6l2 2.2-1 1.4c.7 1.5 1.9 2.7 3.4 3.4l1.4-1 2.2 2-1 2c-4.8-.3-8.7-4.2-9-9z"/></svg>
          044-555 018 273
        </li>
        <li>
          <svg viewBox="0 0 12 12" aria-hidden="true"><path d="M0 2h12v1.2L6 7 0 3.2zM0 4.6l6 3.8 6-3.8V10H0z"/></svg>
          info@tallmarsh-ic.com
        </li>
        <li>
          <svg viewBox="0 0 12 12" aria-hidden="true"><circle cx="6" cy="6" r="6"/></svg>
          www.tallmarsh-ic.com
        </li>
      </ul>
    </div>
  </section>

  <section class="card card--back" aria-label="Business card back">
    <div class="brand">
      <span class="brand__dot"></span>
      <span class="brand__name">TallMarsh Integrity<br>Consulting Ltd.</span>
    </div>
    <p class="tagline">We are a construction management/inspection for the oil and gas industry, as well as general consulting for Asset Management, fleet management.</p>
  </section>

</main>
</body>
</html>
```